Real Estate Company Looking for Business Card Designs for 3 Executives

Hello!
Thanks so much for considering our project! We are a real estate investment company located in Edmonton, Alberta called Bellhaven Group of Companies. We invest/develop both commercial and residential real estate and are looking to create 3 DOUBLE-SIDED business cards for 3 top executives in the company! (for some reason it won't let us select the double-sided option, but yes, the cards are double sided and would be happy to tip extra)

We have certain guidelines that we want our business cards to for sure follow - the back of the Business card has to be the Black Background Version of the Logo which has already been designed and linked as a file (first file). We want the entire back of the card to simply just be the black background logo. In terms of the front of the card, would like to see a smaller version of the white background logo (linked as the second file) in the top left hand corner - of course, feel free to get creative and we can make revisions together along the way! and Then after that, just text. We want the card to be sharp, clean, easy on the eyes and highly professional looking. We would like the card to include the Full name of the Company (Bellhaven Group of Companies), Name of the Person, Title, Phone, Email. If possible please provide the front part of the card for 3 people:

1) Bellhaven Group of Companies, Liora Quenby, Chief Financial Officer, 780-555-0142, lioraquenby@bellhavengroup.example

2) Bellhaven Group of Companies, Tobias Quenby, Chief Executive Officer, 780-555-0187, tobiasquenby@bellhavengroup.example

3) Bellhaven Group of Companies, Rui Delcourt, Chief Operations Officer, 587-555-0163, ruidelcourt@bellhavengroup.example

Thank you so much for considering our project & we look forward to seeing your designs!

```html
<!DOCTYPE html>
<html lang="en">
<head>
<meta charset="utf-8">
<title>Bellhaven Group of Companies — Business Card</title>
<link rel="stylesheet" href="https://fonts.googleapis.com/css2?family=Poppins:wght@300;400;500;600&display=swap">
<style>
  :root {
    --stage: #2a2a2c;
    --card: #1c1d1f;
    --card-back-dark: #0b0b0c;
    --card-back-mid: #2b2b2e;
    --ink: #ffffff;
    --ink-soft: #d9dadc;
    --rule: #6a6b6e;
  }
  * { margin: 0; padding: 0; box-sizing: border-box; }
  html, body {
    width: 1200px; height: 1108px; overflow: hidden;
    background: var(--stage);
    font-family: "Poppins", sans-serif;
    color: var(--ink);
  }
  .stage {
    position: relative; width: 1200px; height: 1108px;
    display: flex; justify-content: center; align-items: center; gap: 70px;
  }
  .card {
    width: 420px; height: 680px; border-radius: 26px;
    position: relative; overflow: hidden;
    box-shadow: 0 18px 40px rgba(0,0,0,.45);
  }
  .card-front {
    background: var(--card);
    display: flex; flex-direction: column; align-items: center;
    padding-top: 150px;
  }
  .brand-name {
    font-weight: 500; font-size: 40px; letter-spacing: 10px;
    margin-right: -10px; color: var(--ink);
  }
  .brand-sub {
    margin-top: 10px; font-weight: 300; font-size: 14px;
    letter-spacing: 4px; color: var(--ink-soft);
  }
  .person { margin-top: 150px; text-align: center; }
  .person-name { font-weight: 600; font-size: 25px; letter-spacing: .5px; }
  .person-title { font-weight: 300; font-size: 17px; color: var(--ink-soft); margin-top: 2px; }
  .contact-divider {
    display: flex; align-items: center; gap: 10px; margin-top: 18px; width: 300px;
  }
  .contact-divider .rule { flex: 1; height: 1px; background: var(--rule); }
  .contact-icons { display: flex; gap: 6px; }
  .contact-icons svg { width: 26px; height: 26px; display: block; }
  .contact-list { list-style: none; text-align: center; margin-top: 12px; font-size: 17px; line-height: 1.5; }
  .card-back {
    background: linear-gradient(135deg, var(--card-back-mid) 0%, var(--card-back-dark) 55%, var(--card-back-mid) 100%);
  }
  .back-pattern { position: absolute; inset: 0; }
  .back-brand {
    position: absolute; left: 0; right: 0; bottom: 150px; text-align: center;
    font-weight: 500; font-size: 28px; letter-spacing: 7px; margin-right: -7px;
  }
</style>
</head>
<body>
<main class="stage">
  <section class="card card-front" aria-label="Card front">
    <div class="brand-name">BELLHAVEN</div>
    <div class="brand-sub">GROUP OF COMPANIES</div>
    <div class="person">
      <div class="person-name">LIORA QUENBY</div>
      <div class="person-title">Chief Financial Officer</div>
    </div>
    <div class="contact-divider">
      <span class="rule"></span>
      <span class="contact-icons">
        <svg viewBox="0 0 26 26" aria-hidden="true"><rect width="26" height="26" rx="6" fill="#fff"/><path d="M8 7c1-1 2 0 3 2s0 2-1 3c1 2 2 3 4 4 1-1 1-2 3-1s3 2 2 3-2 2-4 1c-3-1-6-4-7-7-1-2-1-4 0-5z" fill="#1c1d1f"/></svg>
        <svg viewBox="0 0 26 26" aria-hidden="true"><rect width="26" height="26" rx="6" fill="#fff"/><rect x="6" y="8" width="14" height="10" fill="none" stroke="#1c1d1f" stroke-width="1.6"/><path d="M6 8l7 6 7-6" fill="none" stroke="#1c1d1f" stroke-width="1.6"/></svg>
        <svg viewBox="0 0 26 26" aria-hidden="true"><rect width="26" height="26" rx="6" fill="#fff"/><circle cx="13" cy="13" r="7" fill="none" stroke="#1c1d1f" stroke-width="1.6"/><ellipse cx="13" cy="13" rx="3" ry="7" fill="none" stroke="#1c1d1f" stroke-width="1.2"/><path d="M6 13h14" stroke="#1c1d1f" stroke-width="1.2"/></svg>
      </span>
      <span class="rule"></span>
    </div>
    <ul class="contact-list">
      <li>780-555-0142</li>
      <li>lioraquenby@bellhavengroup.example</li>
      <li>www.bellhavengroup.example</li>
    </ul>
  </section>

  <section class="card card-back" aria-label="Card back">
    <div class="back-pattern" role="img" aria-label="Glossy tone-on-tone repeating monogram pattern"></div>
    <div class="back-brand">BELLHAVEN</div>
  </section>
</main>
</body>
</html>
```